Etiketten für Olivenöl-Intensivcreme
Zielgruppe
Wir produzieren Bio-Food, u.a. Wein und Olivenöl. Jetzt soll eine Olivenöl-Intensivcreme im Bereich Kosmetik auf dem Markt platziert werden. Unsere Zielgruppe hat ein sehr breites Altersspektrum (jung bis alt), ist naturverbunden, tierlieb, gebildet, kritisch-reflektierend, weiß gute Qualität zu schätzen, ist überwiegend weiblich. Die Olivenöl-Intensivcreme hat eine sehr breite Verwendung und soll sich als 'Allzweckwaffe' in jedem Haushalt etablieren (Babyhaut-Pflege, Lippenpflege, Ganzkörperpflege, Hand-Schutzcreme etc.).
Aufgabenstellung
Die Creme soll heißen: Velamira (es könnte z.B. der Buchstabe 'O' durch eine Olive ersetzt werden). Es gibt zwei Etikette (Deckeloberseite der Metalldose und auf dem Boden). Der Durchmesser der Etikette ist jeweils 5,5 cm. Die Deckelunterseite gilt reinen Pflichtangaben. Im Dateidownloadbereich sind die Textvorgaben für die Etikette. MUT zur Farbe! Wir sind NICHT brav und angepasst! Orange kann Akzente setzen bzw. für Aufmerksamkeit im Regal sorgen.

```html
<!DOCTYPE html>
<html lang="de">
<head>
<meta charset="utf-8">
<title>Velamira – Etiketten Olivenöl-Intensivcreme</title>
<link rel="stylesheet" href="https://fonts.googleapis.com/css2?family=Oswald:wght@400;500&family=Roboto+Condensed:wght@700&display=swap">
<style>
  :root {
    --olive-green: #5b8a2b;
    --deep-green: #1f5e1a;
    --accent-orange: #e0721a;
    --splash-dark: #c8621a;
    --splash-light: #f2a04a;
    --tree-blush: #f6c9bd;
    --label-edge: #1b1b1b;
    --paper: #ffffff;
  }
  * { box-sizing: border-box; margin: 0; padding: 0; }
  html, body { width: 1200px; height: 791px; overflow: hidden; background: var(--paper); }
  .sheet { position: relative; width: 1200px; height: 791px; }

  .label {
    position: absolute;
    width: 354px; height: 354px;
    border-radius: 50%;
    border: 2px solid var(--label-edge);
    background: var(--paper);
    overflow: hidden;
  }
  .col-1 { left: 9px; } .col-2 { left: 416px; } .col-3 { left: 829px; }
  .row-1 { top: 32px; } .row-2 { top: 408px; }

  .splash-area, .tree-backdrop, .curved-claim { position: absolute; inset: 0; width: 100%; height: 100%; }

  .tree-mark {
    position: absolute; left: 150px; top: 18px;
    width: 56px; height: 58px;
    border-radius: 8px;
    background: radial-gradient(circle at 50% 45%, var(--splash-light), var(--accent-orange));
    opacity: 0.85;
  }

  .brand {
    position: absolute; left: 0; right: 0; top: 112px;
    display: flex; justify-content: center; align-items: center; gap: 8px;
    font-family: "Oswald", sans-serif; font-weight: 500;
    font-size: 60px; line-height: 1; color: var(--olive-green);
    padding-left: 24px;
  }
  .brand-dot {
    width: 50px; height: 50px; border-radius: 50%;
    background: var(--olive-green);
  }

  .product-name {
    position: absolute; left: 0; right: 0; top: 192px;
    text-align: center; padding-left: 30px;
    font-family: "Oswald", sans-serif; font-weight: 400;
    font-size: 21px; line-height: 1; color: var(--accent-orange);
  }
  .category-tag {
    position: absolute; left: 120px; top: 222px;
    width: 178px; height: 30px;
    background: var(--deep-green); color: var(--paper);
    font-family: "Oswald", sans-serif; font-weight: 400;
    font-size: 21px; line-height: 30px; text-align: center;
  }
  .benefits { list-style: none; font-family: "Roboto Condensed", sans-serif; font-weight: 700; font-size: 13px; color: var(--accent-orange); }
  .benefits li { position: absolute; white-space: nowrap; }
  .benefits li:nth-child(1) { left: 96px; top: 264px; }
  .benefits li:nth-child(2) { left: 156px; top: 284px; }
  .benefits li:nth-child(3) { left: 194px; top: 304px; }

  .curved-claim text { font-family: "Roboto Condensed", sans-serif; font-style: normal; font-weight: 700; font-size: 12px; fill: var(--accent-orange); }
</style>
</head>
<body>
<main class="sheet">

  <svg width="0" height="0" style="position:absolute" aria-hidden="true">
    <defs>
      <linearGradient id="splash-fade" x1="0" y1="0" x2="1" y2="0">
        <stop offset="0" stop-color="#c8621a"/>
        <stop offset="0.45" stop-color="#f2a04a" stop-opacity="0.8"/>
        <stop offset="1" stop-color="#f2a04a" stop-opacity="0"/>
      </linearGradient>
      <radialGradient id="drip-fade" cx="0.5" cy="0.5" r="0.5">
        <stop offset="0" stop-color="#e0721a" stop-opacity="0.55"/>
        <stop offset="1" stop-color="#e0721a" stop-opacity="0"/>
      </radialGradient>
      <radialGradient id="blush-tone" cx="0.6" cy="0.3" r="0.6">
        <stop offset="0" stop-color="#f6c9bd" stop-opacity="0.7"/>
        <stop offset="1" stop-color="#f6c9bd" stop-opacity="0"/>
      </radialGradient>
      <path id="claim-arc" d="M152,326 A152,152 0 0 0 328,160"/>
    </defs>
  </svg>

  <!-- Row 1 -->
  <section class="label col-1 row-1">
    <svg class="splash-area" viewBox="0 0 354 354" role="img" aria-label="Orangefarbener Ölspritzer am linken Rand und oben rechts"><rect x="0" y="0" width="95" height="354" fill="url(#splash-fade)"/><ellipse cx="290" cy="100" rx="55" ry="45" fill="url(#drip-fade)"/></svg>
    <div class="tree-mark" role="img" aria-label="Orangefarbenes Baumsymbol"></div>
    <div class="brand"><span class="brand-dot"></span>Velamira</div>
    <p class="product-name">OLIVENÖL-INTENSIVCREME</p>
    <p class="category-tag">NATURKOSMETIK</p>
    <svg class="curved-claim" viewBox="0 0 354 354"><text><textPath href="#claim-arc">Bio-Olive • Vegan • Pflege - und Schutzcreme</textPath></text></svg>
  </section>

  <section class="label col-2 row-1">
    <svg class="splash-area" viewBox="0 0 354 354" role="img" aria-label="Orangefarbener Ölspritzer am linken Rand und oben rechts"><rect x="0" y="0" width="95" height="354" fill="url(#splash-fade)"/><ellipse cx="290" cy="100" rx="55" ry="45" fill="url(#drip-fade)"/></svg>
    <div class="tree-mark" role="img" aria-label="Orangefarbenes Baumsymbol"></div>
    <div class="brand"><span class="brand-dot"></span>Velamira</div>
    <p class="product-name">OLIVENÖL-INTENSIVCREME</p>
    <p class="category-tag">NATURKOSMETIK</p>
    <ul class="benefits"><li>• Pflege - und Schutzcreme</li><li>• Bio-Olive</li><li>• Vegan</li></ul>
  </section>

  <section class="label col-3 row-1">
    <svg class="tree-backdrop" viewBox="0 0 354 354" role="img" aria-label="Zartrosa Baumkronen im Hintergrund"><ellipse cx="220" cy="90" rx="150" ry="110" fill="url(#blush-tone)"/></svg>
    <svg class="splash-area" viewBox="0 0 354 354" role="img" aria-label="Orangefarbener Ölspritzer am linken Rand und oben rechts"><rect x="0" y="0" width="95" height="354" fill="url(#splash-fade)"/><ellipse cx="305" cy="110" rx="45" ry="45" fill="url(#drip-fade)"/></svg>
    <div class="brand"><span class="brand-dot"></span>Velamira</div>
    <p class="product-name">OLIVENÖL-INTENSIVCREME</p>
    <p class="category-tag">NATURKOSMETIK</p>
    <svg class="curved-claim" viewBox="0 0 354 354"><text><textPath href="#claim-arc">Bio-Olive • Vegan • Pflege - und Schutzcreme</textPath></text></svg>
  </section>

  <!-- Row 2 -->
  <section class="label col-1 row-2">
    <svg class="splash-area" viewBox="0 0 354 354" role="img" aria-label="Orangefarbener Ölspritzer am linken Rand und oben rechts"><rect x="0" y="0" width="95" height="354" fill="url(#splash-fade)"/><ellipse cx="290" cy="100" rx="55" ry="45" fill="url(#drip-fade)"/></svg>
    <div class="tree-mark" role="img" aria-label="Orangefarbenes Baumsymbol"></div>
    <div class="brand">Velamira</div>
    <p class="product-name">OLIVENÖL-INTENSIVCREME</p>
    <p class="category-tag">NATURKOSMETIK</p>
    <svg class="curved-claim" viewBox="0 0 354 354"><text><textPath href="#claim-arc">Bio-Olive • Vegan • Pflege - und Schutzcreme</textPath></text></svg>
  </section>

  <section class="label col-2 row-2">
    <svg class="splash-area" viewBox="0 0 354 354" role="img" aria-label="Orangefarbener Ölspritzer am linken Rand und oben rechts"><rect x="0" y="0" width="95" height="354" fill="url(#splash-fade)"/><ellipse cx="290" cy="100" rx="55" ry="45" fill="url(#drip-fade)"/></svg>
    <div class="tree-mark" role="img" aria-label="Orangefarbenes Baumsymbol"></div>
    <div class="brand">Velamira</div>
    <p class="product-name">OLIVENÖL-INTENSIVCREME</p>
    <p class="category-tag">NATURKOSMETIK</p>
    <ul class="benefits"><li>• Pflege - und Schutzcreme</li><li>• Bio-Olive</li><li>• Vegan</li></ul>
  </section>

  <section class="label col-3 row-2">
    <svg class="tree-backdrop" viewBox="0 0 354 354" role="img" aria-label="Zartrosa Baumkronen im Hintergrund"><ellipse cx="220" cy="90" rx="150" ry="110" fill="url(#blush-tone)"/></svg>
    <svg class="splash-area" viewBox="0 0 354 354" role="img" aria-label="Orangefarbener Ölspritzer am linken Rand und oben rechts"><rect x="0" y="0" width="95" height="354" fill="url(#splash-fade)"/><ellipse cx="305" cy="110" rx="45" ry="45" fill="url(#drip-fade)"/></svg>
    <div class="brand">Velamira</div>
    <p class="product-name">OLIVENÖL-INTENSIVCREME</p>
    <p class="category-tag">NATURKOSMETIK</p>
    <svg class="curved-claim" viewBox="0 0 354 354"><text><textPath href="#claim-arc">Bio-Olive • Vegan • Pflege - und Schutzcreme</textPath></text></svg>
  </section>

</main>
</body>
</html>
```